card for handyman and landscaping business, double sided with services listed on the back

Design a business card for a handyman and Landscaping business in San Jose,ca. Would like front to be a house with 3D characters doing different tasks i.e. Mowing lawn, painting, sprinklers, lighting, weed whacking, power washing, lumber etc. on the backside a cutout of the interior with computer, internet, cleaning, bathroom/kitchen remodeling, smart home etc.

Industry/Entity Type

Handyman

Contact Information for Business Card

Two sided view of a house, one outside services and one inside services

Colors

Designer to choose colors to be used in the design.

Requirements
Must have
• General Household Repairs and Maintenance
• Landscaping, Gardening, and Planting
• Painting, Patching and Trim/Moulding Work
• Cleaning, Restoring and Hauling/Trash Removal
• Blinds, Curtains, and Assembly Work
• Computer, Internet/Wireless, and Smart Home Service

```html
<!DOCTYPE html>
<html lang="en">
<head>
<meta charset="utf-8">
<title>Handyman Landscaping and Tech Services – Business Card</title>
<link rel="stylesheet" href="https://fonts.googleapis.com/css2?family=Montserrat:wght@600&family=Open+Sans:wght@400;700&display=swap">
<style>
  :root {
    --backdrop: #505050;
    --green-light: #2f9e4f;
    --green-dark: #0b4d2b;
    --paper: #f0f0f0;
    --white: #ffffff;
    --heading-font: "Montserrat", sans-serif;
    --body-font: "Open Sans", sans-serif;
  }
  * { margin: 0; padding: 0; box-sizing: border-box; }
  html, body { width: 1200px; height: 900px; overflow: hidden; background: var(--backdrop); }
  .canvas { position: relative; width: 1200px; height: 900px; }

  .card {
    position: absolute;
    height: 271px;
    background: var(--green-dark);
    box-shadow: 2px 3px 6px rgba(0,0,0,.45);
    overflow: hidden;
    color: var(--white);
    font-family: var(--body-font);
  }
  .card--front { left: 150px; top: 306px; width: 437px; }
  .card--back  { left: 608px; top: 306px; width: 440px; }

  .card__header {
    position: absolute; left: 0; top: 0; width: 100%;
    background: var(--green-light);
    font-family: var(--heading-font);
    font-weight: 600;
    display: flex; align-items: center;
  }
  .card--front .card__header { height: 56px; padding-left: 20px; font-size: 15.5px; letter-spacing: .1px; }
  .card--back .card__header { height: 47px; justify-content: center; font-size: 16.5px; }

  .house-band { position: absolute; left: 0; top: 0; }

  .contact {
    position: absolute; left: 22px; top: 73px;
    list-style: none; font-size: 12.5px; line-height: 16px;
  }
  .contact li { display: flex; align-items: center; gap: 6px; }
  .contact svg { width: 9px; height: 9px; fill: var(--white); }
  .contact .address { margin-top: 6px; padding-left: 0; display: block; }

  .person { position: absolute; right: 23px; top: 76px; text-align: right; }
  .person__name { font-weight: 700; font-size: 14.5px; line-height: 17px; }
  .person__title { font-size: 12.5px; line-height: 15px; }

  .services {
    position: absolute; top: 60px; list-style: none;
    font-size: 11.2px; line-height: 14px;
  }
  .services li { position: relative; padding-left: 10px; }
  .services li::before {
    content: ""; position: absolute; left: 0; top: 5px;
    width: 4px; height: 4px; border-radius: 50%; background: var(--white);
  }
  .services--left { left: 16px; }
  .services--right { left: 268px; }

  .icon-row {
    position: absolute; left: 0; width: 100%;
    display: flex; justify-content: center; gap: 15.5px;
  }
  .card--front .icon-row { top: 204px; }
  .card--back .icon-row { top: 206px; gap: 16px; }
  .icon {
    width: 50px; height: 50px; border-radius: 50%;
    background: var(--green-light);
    display: flex; align-items: center; justify-content: center;
  }
  .icon svg { width: 30px; height: 30px; fill: var(--white); stroke: var(--white); }
</style>
</head>
<body>
<main class="canvas">

  <!-- Front side -->
  <section class="card card--front" aria-label="Business card front">
    <svg class="house-band" width="437" height="271" viewBox="0 0 437 271" aria-hidden="true">
      <path d="M0 186 H197 V153 L254 130 L311 153 V186 H437 V271 H0 Z" fill="var(--paper)"/>
      <path d="M0 185.5 H197 V153 L254 130 L311 153 V185.5 H437" fill="none" stroke="var(--green-light)" stroke-width="3"/>
    </svg>

    <header class="card__header">HANDYMAN&nbsp; LANDSCAPING AND TECH SERVICES</header>

    <ul class="contact">
      <li><svg viewBox="0 0 24 24"><path d="M6.6 10.8a15 15 0 0 0 6.6 6.6l2.2-2.2a1 1 0 0 1 1-.25 11.4 11.4 0 0 0 3.6.57 1 1 0 0 1 1 1V20a1 1 0 0 1-1 1A17 17 0 0 1 3 4a1 1 0 0 1 1-1h3.5a1 1 0 0 1 1 1c0 1.25.2 2.45.57 3.57a1 1 0 0 1-.25 1z"/></svg>(044)555018274</li>
      <li><svg viewBox="0 0 24 24"><path d="M2 5h20v14H2z M2 5l10 7 10-7" stroke="var(--green-dark)" stroke-width="1.5"/></svg>hello@oakridgefix.com</li>
      <li><svg viewBox="0 0 24 24"><circle cx="12" cy="12" r="11"/></svg>www.oakridgefix.com</li>
      <li class="address">4817, Linden Grove Ave,<br>San Jose, 95112</li>
    </ul>

    <div class="person">
      <p class="person__name">MARCUS DELGADO</p>
      <p class="person__title">Managing Director</p>
    </div>

    <div class="icon-row">
      <span class="icon" aria-label="Bathroom plumbing"><svg viewBox="0 0 24 24"><rect x="5" y="2" width="14" height="6" rx="1"/><path d="M4 10h16c0 4-3 6-5 6v4H9v-4c-2 0-5-2-5-6z"/></svg></span>
      <span class="icon" aria-label="Cleaning"><svg viewBox="0 0 24 24"><path d="M18 2l1.5 1-5 8" stroke-width="1.8" fill="none"/><path d="M10 11l5 3-4 8c-3-1-6-3-8-5 3 0 5-2 7-6z"/></svg></span>
      <span class="icon" aria-label="Computer and wireless"><svg viewBox="0 0 24 24"><rect x="3" y="4" width="18" height="13" rx="1" fill="none" stroke-width="1.8"/><rect x="8" y="19" width="8" height="2"/><path d="M9 9a4.5 4.5 0 0 1 6 0M10.5 11a2 2 0 0 1 3 0" fill="none" stroke-width="1.3"/></svg></span>
      <span class="icon" aria-label="Internet antenna"><svg viewBox="0 0 24 24"><path d="M12 10l-3 12h6z"/><circle cx="12" cy="9" r="1.6"/><path d="M8 5a6 6 0 0 0 0 8M16 5a6 6 0 0 1 0 8M5 3a9 9 0 0 0 0 12M19 3a9 9 0 0 1 0 12" fill="none" stroke-width="1.4"/></svg></span>
      <span class="icon" aria-label="Lighting"><svg viewBox="0 0 24 24"><path d="M12 5a6 6 0 0 0-3.5 10.9V18h7v-2.1A6 6 0 0 0 12 5z"/><rect x="9" y="19" width="6" height="2.5" rx="1"/><path d="M12 1v2M3 10h2M19 10h2M5 4l1.4 1.4M19 4l-1.4 1.4" stroke-width="1.5"/></svg></span>
      <span class="icon" aria-label="Smart home"><svg viewBox="0 0 24 24"><path d="M12 2L2 11h3v11h14V11h3z"/><circle cx="12" cy="15" r="3.5" fill="none" stroke="var(--green-light)" stroke-width="1.6"/><path d="M12 10.5v4" stroke="var(--green-light)" stroke-width="1.6"/></svg></span>
    </div>
  </section>

  <!-- Back side -->
  <section class="card card--back" aria-label="Business card back">
    <svg class="house-band" width="440" height="272" viewBox="0 0 440 272" aria-hidden="true">
      <path d="M0 188 H127 V153 L185 131 L244 153 V188 H440 V272 H0 Z" fill="var(--paper)"/>
      <path d="M0 187.5 H127 V153 L185 131 L244 153 V187.5 H440" fill="none" stroke="var(--green-light)" stroke-width="3"/>
    </svg>

    <header class="card__header">SERVICES</header>

    <ul class="services services--left">
      <li>Handyman</li>
      <li>Landscaping</li>
      <li>Sprinklers/Irrigation</li>
      <li>Painting</li>
      <li>Electrical</li>
      <li>Lighting</li>
      <li>Power Washing</li>
      <li>Hauling</li>
    </ul>
    <ul class="services services--right">
      <li>Cleaning</li>
      <li>Bath/Kitchen</li>
      <li>Baseboards/Trim/Moulding</li>
      <li>Smart Home</li>
      <li>A/C and Heating</li>
      <li>Blinds, Curtains</li>
      <li>Assembly Services</li>
      <li>Computer/Tech Service</li>
    </ul>

    <div class="icon-row">
      <span class="icon" aria-label="Lawn mowing"><svg viewBox="0 0 24 24"><path d="M3 4l6 8" stroke-width="1.8" fill="none"/><path d="M7 12h10l3 5H5z"/><circle cx="7" cy="19" r="2"/><circle cx="18" cy="19" r="2"/></svg></span>
      <span class="icon" aria-label="Patching and trim"><svg viewBox="0 0 24 24"><path d="M16 2l4 4-9 9-4-4z"/><path d="M7 13l-4 7 7-4" /><rect x="2" y="16" width="20" height="2.5" transform="rotate(20 12 17)"/></svg></span>
      <span class="icon" aria-label="Painting"><svg viewBox="0 0 24 24"><rect x="4" y="2" width="15" height="6" rx="1"/><path d="M19 5h2v6h-9v3" fill="none" stroke-width="1.6"/><rect x="10.5" y="14" width="3" height="8" rx="1"/></svg></span>
      <span class="icon" aria-label="Power washing"><svg viewBox="0 0 24 24"><path d="M2 8h13v3H7l-1 7H3z"/><rect x="15" y="9" width="3" height="1.2"/><path d="M19 9.5l3-3M19 9.5h3M19 9.5l3 3" fill="none" stroke-width="1"/></svg></span>
      <span class="icon" aria-label="Hauling and trash removal"><svg viewBox="0 0 24 24"><rect x="4" y="3" width="16" height="3" rx="1"/><path d="M5 7h14l-1.5 13h-11z"/><circle cx="8" cy="21" r="1.5"/><circle cx="16" cy="21" r="1.5"/></svg></span>
      <span class="icon" aria-label="Windows and blinds"><svg viewBox="0 0 24 24"><rect x="3" y="3" width="18" height="18" fill="none" stroke-width="2"/><path d="M12 3v18M3 12h18" stroke-width="2"/></svg></span>
    </div>
  </section>

</main>
</body>
</html>
```